Cutting Edge Property Services Provider is Looking to Update Business Card Design

We are looking to freshen up our business cards to match our cutting edge technology based image.

KORVANEX - Where Care Finds Its Pulse

More information about our company can be found on our website at www.korvanex-demo.net

We integrate technology in a historically low tech industry.

We have appeared on the Brisk 300/3000 list 2 years in a row and we're previously recognized as the 5th Quickest Rising Firm in San Diego.

Our core colors are blue and white, but are not against accents that might improve our image.

We currently have our Mission Statement on our Business Cards in a folding design:
KORVANEX IS THE LEADING BUILDING SERVICES INNOVATOR. BY COMBINING TECHNOLOGY WITH FUNCTIONAL TOOS THAT IMPROVE EFFICIENCY IN THE WORKPLACE, WE PROVIDE UNPARALLELED SERVICE IN THE INDUSTRY. DEVELOPING LASTING RELATIONSHIPS WITH OUR CLIENTS AND ASSOCIATES IS THE CORNERSTONE OF OUR SUCCESS.

We'd like to convey the image of a cutting edge, technology based company. Want the cards to pop.

Target Market(s)

Commercial Property Managers - 20 to 50 year old professionals

Industry/Entity Type

Business

Requirements
Must have
• Must utilize our logo obviously, but are definitely open to using variations on the logo. Utilizing the components of the logo, but maybe in different configurations or backgrounds, etc...

Must use the Name: KORVANEX.
Can also use KORVANEX PROPERTY SERVICES.

Must include the Mission Statement

Must say: Where Care Finds Its Pulse
Nice to have
• We are considering plastic stock, shaped cards, or folding cards.

Nothing over the top or really expensive, but will consider if it conveys innovation and technology.
Should not have
• No images of toilets, buildings, trees, or anything relating to commercial properties.

We want to convey our technology image.

```html
<!DOCTYPE html>
<html lang="en">
<head>
<meta charset="utf-8">
<title>Korvanex Business Card</title>
<link href="https://fonts.googleapis.com/css2?family=Exo+2:wght@400;500;600&display=swap" rel="stylesheet">
<style>
  :root {
    --brand-blue: #2b5b8f;
    --deep-blue: #1f4f86;
    --card-white: #ffffff;
    --ink-grey: #3a3a3a;
    --muted-grey: #5a5a5a;
    --page-bg: #dfe3e6;
  }
  * { margin: 0; padding: 0; box-sizing: border-box; }
  html, body {
    width: 1200px;
    height: 960px;
    overflow: hidden;
    background: var(--page-bg);
    font-family: "Exo 2", Arial, sans-serif;
  }
  .sheet {
    position: relative;
    width: 1200px;
    height: 960px;
  }
  .card {
    position: absolute;
    left: 250px;
    width: 700px;
    height: 400px;
    border-radius: 16px 80px 16px 80px;
    box-shadow: 0 6px 18px rgba(0, 0, 0, 0.12);
    overflow: hidden;
  }
  .card--front { top: 60px; background: var(--card-white); }
  .card--back { top: 500px; background: var(--deep-blue); color: var(--card-white); }

  /* Front */
  .person { position: absolute; left: 48px; top: 70px; }
  .person__name {
    font-size: 30px; font-weight: 500; color: var(--brand-blue);
    letter-spacing: 0.5px; text-transform: uppercase;
  }
  .person__title { font-size: 20px; color: var(--ink-grey); margin-top: 4px; }

  .contact { position: absolute; left: 48px; top: 200px; list-style: none; }
  .contact__item {
    display: flex; align-items: center; gap: 16px;
    font-size: 20px; color: var(--ink-grey); line-height: 30px;
  }
  .contact__item svg { width: 18px; height: 18px; fill: var(--brand-blue); flex: none; }

  .address {
    position: absolute; left: 48px; top: 322px;
    display: flex; gap: 16px; align-items: flex-start;
    font-size: 20px; color: var(--ink-grey); line-height: 28px; font-style: normal;
  }
  .address svg { width: 18px; height: 22px; fill: var(--brand-blue); margin-top: 2px; flex: none; }

  .brand { position: absolute; right: 40px; top: 95px; text-align: center; width: 270px; }
  .brand__lockup { display: flex; align-items: center; justify-content: center; gap: 12px; }
  .brand__dot {
    width: 34px; height: 34px; border-radius: 50%; background: var(--brand-blue);
  }
  .brand__name {
    font-size: 42px; font-weight: 600; color: var(--brand-blue); letter-spacing: 1px;
  }
  .brand__tagline {
    margin-top: 10px; font-size: 16px; color: var(--brand-blue);
    text-transform: uppercase; letter-spacing: 0.3px;
  }

  /* Back */
  .back-brand {
    position: absolute; top: 80px; left: 0; right: 0;
    display: flex; justify-content: center; align-items: center; gap: 14px;
  }
  .back-brand__dot { width: 34px; height: 34px; border-radius: 50%; background: var(--card-white); }
  .back-brand__name { font-size: 46px; font-weight: 600; letter-spacing: 2px; }
  .mission {
    position: absolute; left: 50px; right: 50px; top: 190px;
    text-align: center; font-size: 17px; line-height: 24px;
    text-transform: uppercase; letter-spacing: 0.5px;
  }
</style>
</head>
<body>
<main class="sheet">

  <section class="card card--front" aria-label="Business card front">
    <div class="person">
      <h1 class="person__name">Delia Marwick</h1>
      <p class="person__title">Project Manager</p>
    </div>

    <ul class="contact">
      <li class="contact__item">
        <svg viewBox="0 0 20 20" aria-hidden="true"><path d="M4 2h10a2 2 0 0 1 2 2v12a2 2 0 0 1-2 2H4zM6 5v2h7V5zm0 4v2h7V9z"/></svg>
        1(800) 555-0147
      </li>
      <li class="contact__item">
        <svg viewBox="0 0 20 20" aria-hidden="true"><path d="M2 4h16v12H2zm2 2v.5l6 4.5 6-4.5V6zm0 3v5h12V9l-6 4.5z"/></svg>
        name@korvanex-demo.net
      </li>
      <li class="contact__item">
        <svg viewBox="0 0 20 20" aria-hidden="true"><path d="M10 1a9 9 0 1 0 0 18 9 9 0 0 0 0-18zm-1 3c1 1 3 1 3 3s-3 2-3 4 2 2 2 4-1 2-2 2a7 7 0 0 1 0-13zm4 9c1-1 2-1 3-1a7 7 0 0 1-3 4z"/></svg>
        www.korvanex-demo.net
      </li>
    </ul>

    <address class="address">
      <svg viewBox="0 0 18 22" aria-hidden="true"><path d="M9 0a8 8 0 0 0-8 8c0 6 8 14 8 14s8-8 8-14a8 8 0 0 0-8-8zm0 11a3 3 0 1 1 0-6 3 3 0 0 1 0 6z"/></svg>
      <span>1450 Harbor Crest Blvd. Suite 210<br>San Diego, CA 92130</span>
    </address>

    <div class="brand">
      <div class="brand__lockup">
        <span class="brand__dot" aria-hidden="true"></span>
        <span class="brand__name">KORVANEX</span>
      </div>
      <p class="brand__tagline">Where Care Finds Its Pulse</p>
    </div>
  </section>

  <section class="card card--back" aria-label="Business card back">
    <div class="back-brand">
      <span class="back-brand__dot" aria-hidden="true"></span>
      <span class="back-brand__name">KORVANEX</span>
    </div>
    <p class="mission">
      KORVANEX is the leading building services innovator. By combining
      technology with functional toos that improve efficiency in the
      workplace, we provide unparalleled service in the industry.
      Developing lasting relationships with our clients and associates
      is the cornerstone of our success.
    </p>
  </section>

</main>
</body>
</html>
```